Clear Harbor Business card

We are a company that owns 2 compliance software programs for TV, Radio and Cable industries as well as an online job board. We need a professional business card that incorproates all three logos.

```html
<!DOCTYPE html>
<html lang="en">
<head>
<meta charset="utf-8">
<title>Clear Harbor Business Card</title>
<link href="https://fonts.googleapis.com/css2?family=Jost:wght@600&family=Open+Sans:wght@400;600;700&display=swap" rel="stylesheet">
<style>
  :root {
    --backdrop: #5b5b5b;
    --card-front: #f3f3f3;
    --card-back: #ffffff;
    --ink: #1d1d1d;
    --navy: #1c1f5e;
    --signal-red: #e2351f;
    --sky: #2a8fd0;
  }
  html, body {
    margin: 0;
    width: 1200px;
    height: 900px;
    overflow: hidden;
    background: var(--backdrop);
    font-family: "Open Sans", sans-serif;
  }
  .stage { position: relative; width: 1200px; height: 900px; }
  .card {
    position: absolute;
    top: 200px;
    width: 310px;
    height: 502px;
    box-sizing: border-box;
  }
  .card--front {
    left: 253px;
    background: var(--card-front);
    border-radius: 60px 0 60px 0;
  }
  .card--back {
    left: 627px;
    background: var(--card-back);
    border-radius: 0 60px 0 60px;
  }
  .brand-row {
    position: absolute;
    display: flex;
    align-items: center;
    gap: 8px;
    font-size: 11px;
    font-weight: 700;
    white-space: nowrap;
  }
  .card--front .brand-row { left: 284px; left: 31px; top: 144px; }
  .brand { display: flex; align-items: center; gap: 4px; }
  .brand--signal { color: var(--navy); }
  .brand--wire { color: var(--signal-red); }
  .brand--talent { color: var(--sky); }
  .brand .dot { width: 8px; height: 8px; border-radius: 50%; background: currentColor; }
  .divider { width: 1px; height: 46px; background: var(--navy); }
  .card--back .brand-row {
    font-size: 16px;
    gap: 14px;
    left: 155px;
    top: 255px;
    transform: translate(-50%, -50%) rotate(-90deg);
  }
  .card--back .divider { height: 76px; }
  .card--back .brand .dot { width: 12px; height: 12px; }
  .contact { position: absolute; left: 32px; top: 300px; color: var(--ink); }
  .contact__name {
    font-family: "Jost", sans-serif;
    font-weight: 600;
    font-size: 21px;
    letter-spacing: 0.6px;
    margin: 0;
    line-height: 1.1;
  }
  .contact__title { font-size: 14.5px; margin: 2px 0 12px; }
  .contact__list { list-style: none; margin: 0; padding: 0; font-size: 14.5px; line-height: 18px; }
  .contact__list li { display: flex; align-items: center; gap: 4px; }
  .contact__list svg { width: 12px; height: 12px; fill: var(--ink); }
  .contact__address { font-size: 14.5px; line-height: 18px; margin: 8px 0 0; }
</style>
</head>
<body>
<main class="stage">
  <section class="card card--front">
    <div class="brand-row">
      <span class="brand brand--signal">Signal Harbor<span class="dot"></span></span>
      <span class="divider"></span>
      <span class="brand brand--wire">Wire Harbor</span>
      <span class="divider"></span>
      <span class="brand brand--talent"><span class="dot"></span>TalentDock</span>
    </div>
    <div class="contact">
      <h1 class="contact__name">DANIEL HART</h1>
      <p class="contact__title">Managing Director</p>
      <ul class="contact__list">
        <li><svg viewBox="0 0 12 12"><path d="M1 4c0-2 2-3 5-3s5 1 5 3l-2 1-1-2H4L3 5zM2 6h8v5H2z"/></svg>044-555 010 200</li>
        <li><svg viewBox="0 0 12 12"><path d="M3 0h6v12H3zM4 1.5v8h4v-8z"/></svg>044-555 010 200</li>
        <li><svg viewBox="0 0 12 12"><path d="M1 2.5h10v7H1zM1.5 3l4.5 3.5L10.5 3"/></svg>info@clearharbor.com</li>
        <li><svg viewBox="0 0 12 12"><circle cx="6" cy="6" r="5.5"/></svg>www.clearharbor.com</li>
      </ul>
      <p class="contact__address">48 Quay Street, Suite 210<br>Port Hollis, 104520.</p>
    </div>
  </section>
  <section class="card card--back">
    <div class="brand-row">
      <span class="brand brand--signal">Signal Harbor<span class="dot"></span></span>
      <span class="divider"></span>
      <span class="brand brand--wire">Wire Harbor</span>
      <span class="divider"></span>
      <span class="brand brand--talent"><span class="dot"></span>TalentDock</span>
    </div>
  </section>
</main>
</body>
</html>
```